Calm and Clear Wellness Flyer (new business startup)

One page...clear enough to be read if faxed. This mental health clinic treats depression/anxiety in kids and adults. It also treats opiate and alcohol addiction. It's in downtown Elmira, NY and the owner of the clinic is from Elmira NY, where it's located. This clinic does not take health insurance, so it charges a low rate of $75 a visit once they pay the $125 starting fee.
Updates

Target Market(s)

doctors offices, new patients

Industry/Entity Type

Doctor

Requirements
Must have
• see microsoft word document. pdf is printed on the company letterhead.
Nice to have
• a simplified map would be nice. if you can include the building it would be a plus. The same two fonts were used in the business cards and letter head (kennedy small caps boo*) and Refrigerator Delux.

```html
<!DOCTYPE html>
<html lang="en">
<head>
<meta charset="utf-8">
<title>Calm and Clear Wellness – Flyer</title>
<link rel="stylesheet" href="https://fonts.googleapis.com/css2?family=Cinzel:wght@500&family=Open+Sans:wght@400;700;800&family=Roboto+Condensed:wght@300;400&display=swap">
<style>
  :root {
    --charcoal: #343434;
    --sky: #29a8e0;
    --orange: #f26a2e;
    --ink: #111111;
    --white: #ffffff;
    --footer-ink: #2b2b2b;
  }
  * { margin: 0; padding: 0; box-sizing: border-box; }
  html, body { width: 849px; height: 1200px; overflow: hidden; background: var(--charcoal); }
  .flyer { position: relative; width: 849px; height: 1200px; overflow: hidden; font-family: "Open Sans", Arial, sans-serif; color: var(--white); }
  .backdrop { position: absolute; inset: 0; }
  .brand { position: absolute; left: 60px; top: 30px; display: flex; align-items: center; gap: 14px; }
  .brand-dot { width: 52px; height: 52px; border-radius: 50%; background: var(--orange); }
  .brand-name { font-family: "Open Sans", Arial, sans-serif; font-weight: 700; font-size: 27px; color: var(--orange); letter-spacing: -0.3px; }
  .practitioner { position: absolute; right: 44px; top: 102px; text-align: right; }
  .practitioner-name { font-family: "Cinzel", Georgia, serif; font-weight: 500; font-size: 40px; color: var(--sky); letter-spacing: 1px; line-height: 1.1; }
  .practitioner-credentials { font-family: "Roboto Condensed", Arial, sans-serif; font-size: 15.5px; margin-top: 6px; }
  .conditions { position: absolute; left: 58px; top: 288px; list-style: none; }
  .conditions li { position: relative; padding-left: 36px; font-weight: 800; font-size: 43px; color: var(--ink); line-height: 1.1; letter-spacing: 0.3px; margin-bottom: 37px; }
  .conditions li::before { content: ""; position: absolute; left: 3px; top: 16px; width: 20px; height: 20px; border-radius: 50%; background: var(--white); }
  .conditions li.two-line { line-height: 1.12; }
  .pricing { position: absolute; left: 93px; top: 858px; }
  .hours { font-weight: 700; font-size: 28px; color: var(--sky); margin-bottom: 6px; }
  .price-row { font-size: 20.5px; line-height: 38px; display: flex; width: 596px; }
  .price-row .fill { flex: 1; overflow: hidden; white-space: nowrap; letter-spacing: 1px; }
  .price-row .fill::after { content: "..................................................................................."; }
  .quote { position: absolute; left: 92px; top: 1030px; font-size: 21.5px; }
  .note { position: absolute; left: 92px; top: 1066px; font-weight: 700; font-size: 13.6px; line-height: 19px; }
  .footer { position: absolute; left: 0; top: 1133px; width: 849px; height: 67px; background: var(--sky); font-family: "Roboto Condensed", Arial, sans-serif; font-weight: 300; font-size: 15.5px; color: var(--footer-ink); line-height: 22px; }
  .footer-left { position: absolute; left: 87px; top: 10px; }
  .footer-right { position: absolute; right: 50px; top: 10px; text-align: right; }
</style>
</head>
<body>
<main class="flyer">
  <svg class="backdrop" width="849" height="1200" viewBox="0 0 849 1200" aria-hidden="false">
    <defs>
      <linearGradient id="building-tone" x1="0" y1="0" x2="0" y2="1">
        <stop offset="0" stop-color="#6aa7df"/>
        <stop offset="0.35" stop-color="#7a4c3c"/>
        <stop offset="0.85" stop-color="#5a4238"/>
        <stop offset="1" stop-color="#9a9a9a"/>
      </linearGradient>
      <linearGradient id="map-tone" x1="0" y1="0" x2="1" y2="1">
        <stop offset="0" stop-color="#eceae5"/>
        <stop offset="0.6" stop-color="#e3e3de"/>
        <stop offset="1" stop-color="#b3d3ee"/>
      </linearGradient>
      <clipPath id="photo-shape">
        <path d="M405,249 Q505,520 522,850 L849,850 L849,258 Q620,256 405,249 Z"/>
      </clipPath>
    </defs>
    <rect class="bg-charcoal" width="849" height="1200" fill="#343434"/>
    <path class="bg-sky-wave" d="M0,97 Q330,250 849,258 L849,850 L0,850 Z" fill="#29a8e0"/>
    <g clip-path="url(#photo-shape)">
      <rect role="img" aria-label="Photo of the downtown brick office building" x="400" y="240" width="449" height="315" fill="url(#building-tone)"/>
      <rect role="img" aria-label="Street map of downtown Elmira with the clinic location pinned" x="400" y="555" width="449" height="295" fill="url(#map-tone)"/>
    </g>
  </svg>

  <header class="brand">
    <span class="brand-dot"></span>
    <span class="brand-name">CALM AND CLEAR WELLNESS</span>
  </header>

  <section class="practitioner">
    <h1 class="practitioner-name">DANIEL REYES, RPA,PLLC</h1>
    <p class="practitioner-credentials">(607) 555-0142 - Phychiatric Physycian Assistant (PA-C-PSY, CAQ ) danielreyes@example.com</p>
  </section>

  <ul class="conditions">
    <li>Depression</li>
    <li>PTSD</li>
    <li>Addiction</li>
    <li>Anxiety</li>
    <li>ADHD</li>
    <li class="two-line">Bipolar Childhood<br>Mood Disorders</li>
  </ul>

  <section class="pricing">
    <h2 class="hours">Hours: Monday and Saturdays 9-4pm</h2>
    <p class="price-row"><span>Psychiatric Evaluation (45min)</span><span class="fill"></span><span>$125*</span></p>
    <p class="price-row"><span>Psychiatric Office Visit (15min)</span><span class="fill"></span><span>$75*</span></p>
    <p class="price-row"><span>Ages:&nbsp; 6 years old and up</span></p>
  </section>

  <p class="quote">“We work for you, not the insurance companies”</p>
  <p class="note">*Although we do not partner with any Health Insurance Companies at this time,<br>a bill will be provided to you at the time of service for youto submit to your insurance company.</p>

  <footer class="footer">
    <div class="footer-left">250 E. Water St #108 Elmira, NY 14901<br>With Dr. Helen Marsh</div>
    <div class="footer-right">(P) 607-555-0142 (F) 607-555-0187<br>www.calmclearwellness.com</div>
  </footer>
</main>
</body>
</html>
```